Wordpress Design Project - Australian Solar Company wants to start FRESH!

About us

Bright Meadow are a renewable energy company based in Perth Australia, but we also have offices all over Asia. We specialise in offering renewable energy solutions (Solar PV Systems and LED Lighting) to residential and commercial customers.

Our current website: www.brightmeadowenergy.com.au

Our needs

This will be a replacement website as we are not happy with our current layout. We have an Australian company doing our SEO and they have recommended a new layout which we wish to go with.

We really want a professional and easy to navigate website that will assist in bringing in more enquiries and phone calls.

Content

We have all the content and will get the design winner to add this after we have chosen the design we like.
It is important that the call to actions are presented well and are visible these are things like the free quote form and our phone number.

The layout as we have advised has been based on SEO research so we wish it to be exactly the same unless otherwise stated.

Call to action

Our main objective of the new website is for people to come to the home page and see us as a professional and reliable company to deal with and enquire further.

We really want as many people as we can to convert to a lead. We want every person that comes to the website to enquire online or call us. We feel it is important to have a contact us/quote form on every page of the website.

Functional requirements

We have a chatterbook and vidstream account so links to these would be needed

Design assets

The logo needs to be displayed as shown in the website layout brief

Colours – we would like fresh, subdued colours that are professional and appealing to the eye. We ask that you do not take the colours from the logo.

Current website dislikes – the things we currently dislike about our current website is that it is hard to find information and there is no clear call to action. The colours are really unappealing as well as it looks cheap not professional.
The graphics that we require for the slider on the home page will have to be given after the winner is chosen but we want there to be three sliders on rotation

- Credibility builder (employee infront of solar panel) that encourages we use all our own employees not subcontractors
- Residential Slider – picture of a couple and solar panel system with a testimonial
- Commercial slider – picture of commercial system with “find out how you can install solar for free* at your business”

Design ideas

The website needs to be mobile friendly as well
It is going to be a total rebuild from the current website as our current website really isn’t working for us.

Target Market(s)

Target Audience

Our target audience are both residential and commercial clients
Residential – we want to attract home owners that are interested in reducing their electricity bill and helping the environment. Generally these people are between the ages of 28-50+ both male and female.

Commercial – We want to appeal to key decision makers within the commercial sphere. For example – CEOs, Company Directors, Operation managers and business owners of any industry. These people will be interested in reducing their electricity bills and creating a clean green image for their business.
Our target audience will generally come to our website to get information and enquire for a quote/ product information.

Industry/Entity Type

Residential

Requirements
Must have
• MUST BE LAID OUT LIKE THIS:

http://www.pagevaultdocs.com/doc/482937105/Website-Layout

Must have Enquire Now forms on every page that read:

Name
Phone Number
How did you hear about us
Message

```html
<!DOCTYPE html>
<html lang="en">
<head>
<meta charset="utf-8">
<title>Bright Meadow – Home</title>
<link href="https://fonts.googleapis.com/css2?family=Roboto+Condensed:wght@400;700&family=Lato:wght@400;700&family=Arimo:wght@400;700&display=swap" rel="stylesheet">
<style>
:root{
  --orange:#d8950f;
  --orange-dark:#b97d08;
  --green:#4f6b12;
  --green-btn:#4e6c16;
  --text:#555;
  --nav-top:#5a5a5a;
  --nav-bot:#2d2d2d;
  --footer:#4d4840;
  --quote-bg:rgba(40,52,72,.88);
}
*{box-sizing:border-box;margin:0;padding:0}
html,body{width:905px;height:1200px;overflow:hidden;background:#fff}
body{position:relative;font-family:"Lato",sans-serif;color:var(--text)}
.abs{position:absolute}
/* header */
.logo{left:108px;top:14px;display:flex;align-items:center;gap:8px}
.logo-dot{width:44px;height:44px;border-radius:50%;background:var(--orange)}
.logo-name{font-family:"Arimo",sans-serif;font-weight:700;font-size:22px;color:var(--green)}
.phone-icon{left:482px;top:38px;width:37px;height:37px;border-radius:50%;background:#a9a9a9}
.experts{left:522px;top:38px;font-family:"Arimo",sans-serif;color:var(--green)}
.experts .label{font-size:12px;display:block}
.experts .num{font-size:15px;display:block;margin-left:10px;margin-top:1px}
.social-square{left:637px;top:41px;width:22px;height:22px;border-radius:4px;background:#4a78b8}
.cart{left:668px;top:36px;width:127px;height:36px;border:1px solid #ddd;box-shadow:0 0 3px #ccc;display:flex;align-items:center;padding-left:6px;gap:5px;font-family:"Arimo",sans-serif;font-size:7.5px;color:#2a4f90}
.cart b{color:#c07d00;font-weight:400}
/* nav */
.nav{left:0;top:116px;width:905px;height:34px;background:linear-gradient(var(--nav-top),var(--nav-bot))}
.nav a{position:absolute;top:0;height:34px;line-height:34px;font-family:"Roboto Condensed",sans-serif;font-weight:700;font-size:11px;color:#fff;text-decoration:none;transform:translateX(-50%)}
.nav a.active{background:var(--orange);width:78px;text-align:center}
/* hero */
.hero{left:105px;top:157px;width:693px;height:292px;background:linear-gradient(160deg,#3f7fc9 0%,#7fb4e6 35%,#2b4f9a 60%,#1c3478 100%)}
.arrow{top:118px;width:28px;height:37px;background:#111;display:flex;align-items:center;justify-content:center}
.quote{left:445px;top:37px;width:204px;height:191px;background:var(--quote-bg);padding:12px 11px}
.quote h2{font-family:"Roboto Condensed",sans-serif;font-weight:700;font-size:14px;color:#fff;text-align:center;margin-bottom:9px}
.field{background:#fff;border-radius:3px;height:21px;margin-bottom:8.5px;font-family:"Arimo",sans-serif;font-size:9px;color:#222;padding:5px 6px}
.submit{margin-left:auto;width:87px;height:23px;background:linear-gradient(#f0b020,var(--orange-dark));border-radius:2px;font-family:"Roboto Condensed",sans-serif;font-weight:700;font-size:10.5px;color:#2a2a2a;text-align:center;line-height:23px}
/* services */
.svc{width:162px;top:463px}
.svc h3{font-family:"Roboto Condensed",sans-serif;font-weight:400;font-size:11px;color:var(--green);line-height:17.5px;text-transform:uppercase}
.svc .pic{width:162px;height:91px;margin-top:9px;border:1px solid #ccc}
.svc p{font-size:9px;line-height:14px;margin-top:6px;color:#444}
.btn-green{display:inline-block;margin-top:8px;background:var(--green-btn);color:#fff;font-family:"Roboto Condensed",sans-serif;font-size:8.5px;padding:4px 5px;border-radius:2px}
/* welcome */
.sec-title{font-family:"Roboto Condensed",sans-serif;font-weight:700;font-size:11px;color:var(--green);top:675px}
.welcome-pic{left:105px;top:714px;width:217px;height:125px;background:linear-gradient(160deg,#c9dcef 0%,#3a66b0 45%,#1f3d85 100%)}
.body-txt{font-size:8.4px;line-height:15.6px;color:#666}
.side-txt{left:338px;top:710px;width:178px}
.side-txt p+p{margin-top:3px}
.full-txt{left:106px;top:857px;width:410px}
.full-txt p+p{margin-top:3px}
.testi-pic{left:546px;top:712px;width:252px;height:163px;background:linear-gradient(160deg,#2f66c2 0%,#3b6fc8 50%,#1e3e84 80%,#7a6a60 100%)}
.play{left:118px;top:67px;width:26px;height:26px;border-radius:50%;background:#444;border:2px solid #ddd}
.pv-title{left:547px;top:882px;font-size:12px;color:var(--green)}
.pv-txt{left:547px;top:903px;width:250px}
.posted{left:547px;top:958px;font-family:"Roboto Condensed",sans-serif;font-size:8.5px;color:var(--green)}
/* footer */
.footer{left:0;top:1005px;width:905px;height:195px;background:var(--footer);color:#fff}
.footer h4{position:absolute;top:18px;font-family:"Arimo",sans-serif;font-weight:700;font-size:12px;color:#fff}
.flist{position:absolute;left:106px;top:40px;list-style:none;font-size:8.6px;line-height:14.8px}
.member-pic{left:274px;top:49px;width:56px;height:50px;background:linear-gradient(#d8d2c8,#8a6a55);border:1px solid #eee}
.member-name{left:341px;top:54px;font-size:8px;font-weight:700}
.member-quote{left:341px;top:70px;font-size:8.6px;line-height:11.5px;width:120px}
.req-txt{left:482px;top:47px;width:180px;font-size:8.4px;line-height:15.6px}
.fbtn{top:122px;width:171px;height:29px;background:var(--orange-dark);color:#2a2a2a;font-family:"Arimo",sans-serif;font-weight:700;font-size:11px;text-align:center;line-height:29px}
.connect{left:708px;top:44px;font-size:11px}
.connect li{list-style:none;display:flex;align-items:center;gap:8px;height:27px}
.connect i{width:20px;height:20px;border-radius:50%;background:#fff;border:3px solid #d8dbe6;display:inline-block}
.addr{left:712px;top:125px;font-family:"Arimo",sans-serif;font-size:8.5px;line-height:13px}
.copy{left:0;width:905px;top:178px;text-align:center;font-family:"Roboto Condensed",sans-serif;font-weight:700;font-size:8.6px;color:#ddd}
</style>
</head>
<body>

<header>
  <div class="abs logo"><span class="logo-dot"></span><span class="logo-name">Bright Meadow</span></div>
  <div class="abs phone-icon">
    <svg width="37" height="37" viewBox="0 0 37 37"><path d="M13 10c2 0 3 4 2 5l-1 1c1 3 3 5 6 6l1-1c1-1 5 0 5 2s-2 4-4 4C14 27 10 22 10 14c0-2 1-4 3-4z" fill="#fff"/></svg>
  </div>
  <div class="abs experts"><span class="label">ASK OUR EXPERTS</span><span class="num">0390 555 274</span></div>
  <div class="abs social-square"></div>
  <div class="abs cart">
    <svg width="20" height="16" viewBox="0 0 20 16"><path d="M1 2h3l2 8h10l2-6H5" fill="none" stroke="#333" stroke-width="1.4"/><circle cx="8" cy="13" r="1.5" fill="#333"/><circle cx="15" cy="13" r="1.5" fill="#333"/></svg>
    <span>YOUR CART IS <b>: 0 ITEMS</b></span>
  </div>
</header>

<nav class="abs nav">
  <a class="active" style="left:171px">HOME</a>
  <a style="left:246px">SERVICES</a>
  <a style="left:322px">NEWS</a>
  <a style="left:399px">PRODUCTS</a>
  <a style="left:481px">MEDIA</a>
  <a style="left:569px">INFORMATION</a>
  <a style="left:665px">ENQUIRY</a>
  <a style="left:748px">CONTACT US</a>
</nav>

<section class="abs hero" role="img" aria-label="Solar panel array under a bright sun and blue sky">
  <div class="abs arrow" style="left:0"><svg width="10" height="14"><path d="M8 1L2 7l6 6" fill="none" stroke="#fff" stroke-width="2"/></svg></div>
  <div class="abs arrow" style="right:0"><svg width="10" height="14"><path d="M2 1l6 6-6 6" fill="none" stroke="#fff" stroke-width="2"/></svg></div>
  <form class="abs quote">
    <h2>QUOTE ONLINE</h2>
    <div class="field">Name :</div>
    <div class="field">Phone :</div>
    <div class="field">How did you hear about us :</div>
    <div class="field">Message :</div>
    <div class="submit">SUBMIT</div>
  </form>
</section>

<section>
  <div class="abs svc" style="left:105px;top:463px">
    <h3>Perth<br>Residential Solar Power</h3>
    <div class="pic" role="img" aria-label="Industrial plant with pipes" style="background:linear-gradient(#7ba3d8,#c8ccd0 60%,#888)"></div>
    <p>Nemo enim ipsam voluptatem quia vptas sit &nbsp;aut odit aut fugit.</p>
    <span class="btn-green">READ MORE</span>
  </div>
  <div class="abs svc" style="left:282px;top:460px">
    <h3>Perth<br>Commercial&nbsp; Solar Power</h3>
    <div class="pic" role="img" aria-label="Street lights along a road at night" style="background:linear-gradient(#0c0c14,#1a1a2a 60%,#3a2a20)"></div>
    <p>Nemo enim ipsam voluptatem quia vptas sit &nbsp;aut odit aut fugit.</p>
    <span class="btn-green">READ MORE</span>
  </div>
  <div class="abs svc" style="left:460px;top:460px">
    <h3>Perth<br>Air Conditioning WA</h3>
    <div class="pic" role="img" aria-label="Wind turbine and solar panel in a green field below mountains" style="background:linear-gradient(#6f9fd6,#a9c0d8 40%,#6a9a40 60%,#4f7e2a)"></div>
    <p>Nemo enim ipsam voluptatem quia vptas sit &nbsp;aut odit aut fugit.</p>
    <span class="btn-green">READ MORE</span>
  </div>
  <div class="abs svc" style="left:635px;top:460px">
    <h3>Perth<br>LED&nbsp; Lighting</h3>
    <div class="pic" role="img" aria-label="Solar water heater on a rooftop" style="background:linear-gradient(#9fc4e8,#d8dde2 55%,#b8b8b8)"></div>
    <p>Nemo enim ipsam voluptatem quia vptas sit &nbsp;aut odit aut fugit.</p>
    <span class="btn-green">READ MORE</span>
  </div>
</section>

<section>
  <h2 class="abs sec-title" style="left:106px">WELCOME TO BRIGHT MEADOW</h2>
  <div class="abs welcome-pic" role="img" aria-label="Rows of solar panels under a pale sky"></div>
  <div class="abs body-txt side-txt">
    <p>New lighting technology which uses significantly less power consumption and their life span is up to 25 times longer than traditional lightinglighting technology which uses significantly less power</p>
    <p>consumption and their life span is up to 25 times longer than traditional lightinglighting technology which uses significantly less power consumption and their life span is up,</p>
  </div>
  <div class="abs body-txt full-txt">
    <p>Bright Meadow are the Air Conditioning specialists in the industry. We offer top brands, dedicated service and outstanding value for money.New lighting technology which uses significantly less power consumption and their life span is up to 25 times longer than traditional lightinglighting technology which uses significantly less power</p>
    <p>consumption and their life span is up to 25 times longer than traditional lightinglighting technology which uses significantly less power consumption and their life span is up, Bright Meadow are the Air Conditioning specialists in the industry. We offer top brands, dedicated service and outstanding value for money.</p>
  </div>

  <h2 class="abs sec-title" style="left:546px">TESTIMONIALS</h2>
  <div class="abs testi-pic" role="img" aria-label="Installer lifting a solar panel on a roof, video">
    <div class="abs play"><svg width="22" height="22"><path d="M8 6l8 5-8 5z" fill="#ddd"/></svg></div>
  </div>
  <div class="abs pv-title">Photovoltaic</div>
  <p class="abs body-txt pv-txt">All our home Solar Panels are of high quality with long lifetime guarantees.home Solar Panels are of high quality with long. home Solar Panels are of high quality with long</p>
  <div class="abs posted">Past on 21 jul 2013</div>
</section>

<footer class="abs footer">
  <h4 style="left:106px">Products / Services</h4>
  <ul class="flist">
    <li>Perth led lighting</li><li>Solar leasing</li><li>Air Conditioning WA</li><li>Solar Systems</li><li>Residential</li><li>Commercial</li><li>Electrical Systems</li><li>Refrigeration Systems</li>
  </ul>

  <h4 style="left:273px">Become A Membership</h4>
  <div class="abs member-pic" role="img" aria-label="Member portrait"></div>
  <div class="abs member-name">LOREM IPSUM</div>
  <div class="abs member-quote">"Lorem ipsum dolor sit amet, consectetur adipisicing elit</div>
  <div class="abs fbtn" style="left:273px">BECOME A MEMBERSHIP</div>

  <h4 style="left:481px;top:17px">Request quotation</h4>
  <p class="abs req-txt">All our home Solar Panels are of high quality with long lifetime guarantees.home Solar Panels are of high quality with long. home</p>
  <div class="abs fbtn" style="left:480px">REQUEST QUOTATION</div>

  <h4 style="left:706px;top:20px">Connect</h4>
  <ul class="abs connect">
    <li><i></i>Chatterbook</li>
    <li><i></i>Tweetline</li>
    <li><i></i>Email Us</li>
  </ul>
  <div class="abs addr">no : 15,street name<br>city, contry<br>zip code :1111</div>
  <div class="abs copy">Copyright © 2012 Bright Meadow. All rights reserved</div>
</footer>

</body>
</html>
```